General contractor/GM consaltant business card

I need a card for my contracting company in North Dakota, we build industrial buildings for the oil feild and oil feild related companies offices, shops, airplain hangars, airports ext. We have a familly atmosphere on the job and are very relational and personal.
Industry/Entity Type
Industrial
Contact Information for Business Card
Ridgepost Contractors LLC.
Derek T.Holloway
4837 Tamarind dr. Colorado Springs, CO. 80917
Cell# 406-555-0148
derek@ridgepostcontractors.com

```html
<!DOCTYPE html>
<html lang="en">
<head>
<meta charset="utf-8">
<title>Ridgepost Contractors LLC. – Business Card</title>
<link rel="stylesheet" href="https://fonts.googleapis.com/css2?family=Arimo:wght@400;700&display=swap">
<style>
  :root {
    --canvas-bg: #e9e7e3;
    --card-bg: #ffffff;
    --card-shade: #f1f1f1;
    --brand-red: #d9232b;
    --brand-blue: #2d5fb4;
    --ink: #1b1b1b;
  }
  * { box-sizing: border-box; margin: 0; padding: 0; }
  html, body { width: 1200px; height: 858px; overflow: hidden; }
  body {
    background: var(--canvas-bg);
    font-family: "Arimo", Arial, sans-serif;
    display: flex;
    align-items: center;
    justify-content: center;
    gap: 90px;
  }
  .card {
    position: relative;
    width: 400px;
    height: 700px;
    background: linear-gradient(160deg, var(--card-bg) 40%, var(--card-shade) 100%);
    box-shadow: 0 6px 18px rgba(0,0,0,.18);
    overflow: hidden;
  }
  .brand {
    position: absolute;
    left: 0; right: 0;
    display: flex;
    align-items: center;
    justify-content: center;
    gap: 10px;
  }
  .brand-dot {
    width: 18px; height: 18px;
    border-radius: 50%;
    background: var(--brand-blue);
    flex: none;
  }
  .brand-name {
    color: var(--brand-red);
    font-weight: 700;
    font-size: 23px;
    white-space: nowrap;
  }
  .person-name {
    position: absolute;
    color: var(--ink);
    font-size: 31px;
    font-weight: 400;
    white-space: nowrap;
  }
  .contact {
    position: absolute;
    left: 48px;
    top: 330px;
    list-style: none;
    color: var(--brand-red);
    font-size: 20px;
    line-height: 1.35;
  }
  .card--front .brand { top: 80px; }
  .card--front .person-name { left: 0; right: 0; top: 185px; text-align: center; }
  .card--back .brand { top: 210px; }
  .card--back .person-name { right: 40px; top: 520px; }
</style>
</head>
<body>
  <section class="card card--front" aria-label="Card front">
    <div class="brand">
      <span class="brand-dot"></span>
      <span class="brand-name">Ridgepost Contractors LLC.</span>
    </div>
    <p class="person-name">Derek T.Holloway</p>
    <ul class="contact">
      <li>406-555-0148</li>
      <li>derek@ridgepostcontractors.com</li>
      <li>4837 Tamarind dr.</li>
      <li>Colorado Springs, CO. 80917</li>
    </ul>
  </section>

  <section class="card card--back" aria-label="Card back">
    <div class="brand">
      <span class="brand-dot"></span>
      <span class="brand-name">Ridgepost Contractors LLC.</span>
    </div>
    <p class="person-name">Derek T.Holloway</p>
  </section>
</body>
</html>
```